Business Card for Professional Photographer

I'm looking for an eye catching modern clean design that compliments my logo/ website fonts & colours.
I specialise in architecture, corporate & commercial photography so I'm marketing to professional clients rather than portrait / wedding clients.

I would prefer to not have a solid black design.

My logo brand guide is as follows :

Main front font. : Reislust
Main font colour : #fff
Slogan front font : Ubuntu Bold
Monogram front font : Venti Medium
Container colour : #fff

I need print ready files in pdf .png & .eps formats.

Included in the files below are some screen grabs as reference to font & colours etc.

```html
<!DOCTYPE html>
<html lang="en">
<head>
<meta charset="utf-8">
<title>Clear Angle – Business Card</title>
<link rel="stylesheet" href="https://fonts.googleapis.com/css2?family=Ubuntu:wght@300;400;700&family=Roboto+Condensed:wght@700&family=Roboto:wght@400&display=swap">
<style>
  :root {
    --backdrop: #b9b9b9;
    --gold-deep: #b88f3c;
    --gold-mid: #d6b968;
    --gold-pale: #ece09a;
    --gold-text: #b98a3a;
    --ink: #161412;
    --paper: #f7f7f6;
    --body-text: #2b2b2b;
  }
  * { margin: 0; padding: 0; box-sizing: border-box; }
  html, body { width: 1200px; height: 576px; overflow: hidden; }
  body {
    background: var(--backdrop);
    position: relative;
    font-family: "Roboto", Arial, sans-serif;
  }
  .card {
    position: absolute;
    top: 138px;
    width: 484px;
    height: 294px;
    border-radius: 10px;
    overflow: hidden;
  }
  /* Front */
  .card--front {
    left: 81px;
    background: linear-gradient(100deg, var(--gold-deep) 0%, var(--gold-mid) 45%, var(--gold-pale) 100%);
  }
  .front-brand {
    position: absolute;
    left: 151px;
    top: 120px;
    display: flex;
    align-items: center;
    gap: 16px;
  }
  .brand-mark {
    width: 16px;
    height: 16px;
    background: var(--ink);
    flex: none;
  }
  .brand-name {
    font-family: "Ubuntu", Arial, sans-serif;
    font-weight: 300;
    font-size: 26px;
    letter-spacing: 5.4px;
    color: var(--ink);
    line-height: 1;
    white-space: nowrap;
  }
  .brand-tagline {
    font-family: "Ubuntu", Arial, sans-serif;
    font-weight: 700;
    font-size: 8px;
    letter-spacing: 2.9px;
    color: var(--ink);
    margin-top: 6px;
    white-space: nowrap;
  }
  .front-web {
    position: absolute;
    left: 0; right: 0;
    top: 257px;
    text-align: center;
    font-family: "Ubuntu", Arial, sans-serif;
    font-size: 14px;
    letter-spacing: 2.5px;
    color: var(--ink);
  }
  /* Back */
  .card--back {
    left: 602px;
    background: var(--paper);
  }
  .back-brand {
    position: absolute;
    right: 24px;
    top: 38px;
    text-align: right;
  }
  .back-brand .brand-name { color: var(--gold-text); letter-spacing: 5px; }
  .back-brand .brand-tagline { color: var(--gold-text); margin-top: 5px; letter-spacing: 2.9px; }
  .person {
    position: absolute;
    right: 24px;
    top: 136px;
    text-align: right;
  }
  .person-name {
    font-family: "Roboto Condensed", Arial, sans-serif;
    font-weight: 700;
    font-size: 18px;
    color: var(--gold-text);
  }
  .person-role {
    font-size: 13px;
    color: var(--body-text);
    margin-top: 2px;
  }
  .contacts {
    position: absolute;
    right: 24px;
    top: 197px;
    list-style: none;
    text-align: right;
    font-size: 13px;
    color: var(--body-text);
  }
  .contacts li {
    display: flex;
    justify-content: flex-end;
    align-items: center;
    gap: 10px;
    height: 18.5px;
  }
  .contacts svg { width: 11px; height: 11px; fill: var(--gold-mid); }
  .contacts .address { margin-top: 5px; }
</style>
</head>
<body>
  <section class="card card--front" aria-label="Card front">
    <div class="front-brand">
      <div class="brand-mark"></div>
      <div>
        <div class="brand-name">CLEAR ANGLE</div>
        <div class="brand-tagline">Architecture Corporate Commercial</div>
      </div>
    </div>
    <div class="front-web">www.clearangle.com.au</div>
  </section>

  <section class="card card--back" aria-label="Card back">
    <div class="back-brand">
      <div class="brand-name">CLEAR ANGLE</div>
      <div class="brand-tagline">Architecture Corporate Commercial</div>
    </div>
    <div class="person">
      <div class="person-name">Mark Ellison</div>
      <div class="person-role">Photographer</div>
    </div>
    <ul class="contacts">
      <li>0412558017
        <svg viewBox="0 0 12 12" aria-hidden="true"><path d="M2.5 1 L4.5 1 L5 3.5 L3.8 4.5 Q5 7 7.5 8.2 L8.5 7 L11 7.5 L11 9.5 Q10.5 11 9 11 Q1 10 1 3 Q1 1.5 2.5 1 Z"/></svg>
      </li>
      <li>info@clearangle.com.au
        <svg viewBox="0 0 12 12" aria-hidden="true"><path d="M0.5 2.5 H11.5 V9.5 H0.5 Z M1.5 3.2 L6 6.5 L10.5 3.2" stroke="#fff" stroke-width="0.8"/></svg>
      </li>
      <li>www.clearangle.com.au
        <svg viewBox="0 0 12 12" aria-hidden="true"><circle cx="6" cy="6" r="5.5"/><path d="M0.5 6 H11.5 M6 0.5 V11.5 M6 0.5 Q2.5 6 6 11.5 M6 0.5 Q9.5 6 6 11.5" stroke="#fff" stroke-width="0.7" fill="none"/></svg>
      </li>
      <li class="address">48 Harbour Rd Portland Vic 3305</li>
    </ul>
  </section>
</body>
</html>
```